Web Design Project

Psychotherapy and Counselling Practice needs a landing page web design.

My business "Larkfield Advisory" specialises in the treatment of Anxiety and Depression with a holistic approach, endeavouring to unlock the key that holds us to ransom in a life that is imbalanced, frustrating, and ultimately of our own making due to our own perceptions and behaviours.

There is much that impacts us which we cannot change, but we are always in control of how we think, and how we frame our experiences.....learning to challenge those thoughts and behaviours that are destructive and disempowering opens up a world of joyful possibility. Life is about making choices, learn to make wiser and healthier choices.......

Larkfield Advisory has a client base of individual clients but will seek to expand to offer services to the Corporate world by offering an adjunct to employers for established "Wellness Programs".

Larkfield Advisory is a highly professional, ethically bound business, with the needs of the client at the forefront of all we do.

Larkfield Advisory wishes to avoid the usual "jargon driven" psychobabble offered on many counselling web pages. It aims to be stylishly presented, clean in look and with as few "words" as possible and a largely white background (faster loading and more powerful impact of what is stated), those words contained in the webpage should be meaningful, persuasive and have an impact simply at glance. Larkfield does not want , or expect, those prospective clients in need of support , to be reading through volumes of industry driven cliches.

At this point Larkfield is just looking for a high quality landing page. However in time this will likely expand to include other sections such as case studies, video content etc.

Target Market(s)

Those in need of emotional support, suffering mental health issues, and those simply wanting to become self aware supported by a mindful therapist.

Industry/Entity Type

Industry

Requirements
Must have
• The design must incorporate the Larkfield logo and colour schemes found on the attached files.

```html
<!DOCTYPE html>
<html lang="en">
<head>
<meta charset="utf-8">
<title>Larkfield Advisory</title>
<link href="https://fonts.googleapis.com/css2?family=Encode+Sans+Semi+Condensed:wght@400;700&family=Raleway:wght@300&display=swap" rel="stylesheet">
<style>
  :root {
    --green: #82a914;
    --green-soft: #a6c94e;
    --green-pale: #cfe39a;
    --leaf-light: #b5d66a;
    --leaf-deep: #7fae2a;
    --ink: #3c3c3c;
    --nav-ink: #4a4a4a;
    --body-grey: #8a8a8a;
    --bg-light: #ffffff;
    --bg-edge: #d9d9d9;
  }
  * { box-sizing: border-box; margin: 0; padding: 0; }
  html, body { width: 1200px; height: 660px; overflow: hidden; }
  body {
    position: relative;
    background: radial-gradient(ellipse 700px 420px at 600px 330px, var(--bg-light) 0%, #ececec 60%, var(--bg-edge) 100%);
    font-family: "Encode Sans Semi Condensed", "Arial Narrow", sans-serif;
    color: var(--ink);
  }

  .brand {
    position: absolute;
    left: 0; width: 1200px; top: 68px;
    text-align: center;
    font-family: "Raleway", sans-serif;
    font-weight: 300;
    font-size: 29px;
    letter-spacing: 1px;
    color: var(--green);
  }

  .nav-band {
    position: absolute;
    left: 0; top: 164px; width: 1200px; height: 41px;
    background: var(--green);
  }
  .nav-menu {
    position: absolute;
    left: 233px; top: 164px; width: 733px; height: 41px;
    background: linear-gradient(#f6f6f6, #ebebeb);
    border: 1px solid #d2d2d2;
    display: flex; justify-content: center; align-items: center; gap: 17px;
    padding-left: 90px; padding-right: 80px;
    list-style: none;
  }
  .nav-menu li {
    font-size: 19px;
    letter-spacing: -1.5px;
    color: var(--nav-ink);
    line-height: 1;
    white-space: nowrap;
  }

  .card-row-shadow {
    position: absolute;
    left: 230px; top: 395px; width: 740px; height: 50px;
    border-radius: 50%;
    background: radial-gradient(ellipse at center, rgba(0,0,0,0.16), rgba(0,0,0,0) 70%);
  }

  .card { position: absolute; top: 222px; width: 240px; height: 200px; }
  .card-leaf {
    position: absolute;
    left: 24px; top: 53px; width: 208px; height: 143px;
    background: linear-gradient(180deg, var(--leaf-light), var(--leaf-deep));
  }
  .card-face {
    position: absolute;
    left: 0; top: 0; width: 184px; height: 184px;
    border-radius: 50%;
    background: radial-gradient(circle at 50% 40%, #ffffff 55%, #ececec 100%);
    border: 2px solid var(--green-pale);
    text-align: center;
    padding-top: 32px;
  }
  .card-title {
    font-weight: 700;
    font-size: 18px;
    letter-spacing: -1.2px;
    line-height: 1;
    color: var(--green);
  }
  .card-text {
    margin: 14px auto 0;
    width: 146px;
    font-size: 11.5px;
    line-height: 14.4px;
    letter-spacing: -0.6px;
    color: var(--body-grey);
  }
  .card-link {
    position: absolute;
    left: 0; width: 184px; top: 153px;
    font-weight: 700;
    font-size: 11px;
    letter-spacing: -0.5px;
    color: var(--green);
  }

  .social {
    position: absolute;
    left: 485px; top: 495px;
    display: flex; gap: 10px;
    list-style: none;
  }
  .social li {
    width: 50px; height: 50px;
    border-radius: 50%;
    background: var(--green-soft);
    border: 2px solid var(--green);
  }

  .footer {
    position: absolute;
    left: 0; width: 1200px; top: 606px;
    text-align: center;
    font-size: 19px;
    letter-spacing: -1.2px;
    color: #333;
  }
</style>
</head>
<body>
  <div class="brand">LARKFIELD</div>

  <div class="nav-band"></div>
  <ul class="nav-menu">
    <li>HOME</li>
    <li>ABOUT US</li>
    <li>TREATMENTS</li>
    <li>SERIVCES</li>
    <li>CASE STUDIES</li>
    <li>CONTACT US</li>
  </ul>

  <div class="card-row-shadow"></div>

  <section class="card" style="left:272px">
    <div class="card-leaf" role="img" aria-label="Green leaf illustration behind the card"></div>
    <div class="card-face">
      <h2 class="card-title">ABOUT US</h2>
      <p class="card-text">Larkfield Advisory is a highly profession;la, ethically bound business with the needs of the clients at the forefront of all we do.</p>
      <div class="card-link">Read More</div>
    </div>
  </section>

  <section class="card" style="left:500px">
    <div class="card-leaf" role="img" aria-label="Green leaf illustration behind the card"></div>
    <div class="card-face">
      <h2 class="card-title">TREATMENTS</h2>
      <p class="card-text">Treatment of Anxiety and Depression with holistic approach, endeavouring to unloack the key that holds us ransom in a life</p>
      <div class="card-link">Read More</div>
    </div>
  </section>

  <section class="card" style="left:724px">
    <div class="card-leaf" role="img" aria-label="Green leaf illustration behind the card"></div>
    <div class="card-face">
      <h2 class="card-title">SERVICES</h2>
      <p class="card-text">Psychotherapy &amp; Counselling Practice, Wellness Programs, Individual clients.<br>Corporate services</p>
      <div class="card-link">Read More</div>
    </div>
  </section>

  <ul class="social" aria-label="Social links">
    <li></li><li></li><li></li><li></li>
  </ul>

  <div class="footer">© 2013 LARKFIELD</div>
</body>
</html>
```